Wir suchen ein kreatives Einladungskarten-Design
Zielgruppe
Terminierung / Organisation für Steuerberater, Rechtsanwälte Wirtschaftsprüfer und Notare.
Aufgabenstellung
Nicht verspielt, ansprechend, jung, kreativ,
20 jähriges Firmenjubiläum am 30.11.2018 um 17:00 Uhr
Motto: Feuer (in dir muss brennen was du in anderen entzünden willst)
Dies sollte aber sehr elegant und nicht kitschig dargestellt werden.
Eventuell werden wir zur Einladung ein scharfes Gewürz beilegen
Save the date
And celebrate with us
20 Jahre BKL
Freitag, 30.11.18, 17:00 Uhr
Seien Sie dabei, wir freuen uns auf Sie!
Wir bitten um Rückmeldung bis spätestens 31.10.18
Lindenweg 27 94116 Cham

```html
<!DOCTYPE html>
<html lang="de">
<head>
<meta charset="utf-8">
<title>Feuer – 20 jähriges Firmenjubiläum</title>
<link href="https://fonts.googleapis.com/css2?family=Saira+Condensed:wght@200;300;700;800&display=swap" rel="stylesheet">
<style>
  :root {
    --bg: #2b2929;
    --ink: #ffffff;
    --dark: #231f1f;
    --flame-hot: #ffb21e;
    --flame: #e5521a;
    --ember: #5a1a10;
  }
  html, body {
    margin: 0;
    padding: 0;
    overflow: hidden;
    background: var(--bg);
  }
  .card {
    position: relative;
    width: 846px;
    height: 1200px;
    overflow: hidden;
    background: var(--bg);
    color: var(--ink);
    font-family: "Saira Condensed", "Arial Narrow", sans-serif;
  }
  .fire-photo {
    position: absolute;
    left: 0;
    top: 230px;
    width: 846px;
    height: 720px;
    background:
      radial-gradient(ellipse 34% 40% at 52% 55%, var(--flame-hot) 0%, rgba(255,150,30,0.7) 35%, rgba(229,82,26,0) 75%),
      radial-gradient(ellipse 60% 55% at 52% 65%, var(--flame) 0%, var(--ember) 55%, rgba(43,41,41,0) 100%);
  }
  .date-day {
    position: absolute;
    left: 30px;
    top: 2px;
    margin: 0;
    font-size: 196px;
    font-weight: 800;
    line-height: 1;
    letter-spacing: -4px;
  }
  .date-month {
    position: absolute;
    left: 33px;
    top: 172px;
    margin: 0;
    font-size: 41px;
    font-weight: 200;
    line-height: 1;
  }
  .event-info {
    position: absolute;
    right: 34px;
    top: 22px;
    text-align: right;
    margin: 0;
  }
  .company-name {
    margin: 0;
    font-size: 53px;
    font-weight: 700;
    line-height: 1;
  }
  .event-line {
    margin: 0;
    font-size: 42px;
    font-weight: 200;
    line-height: 1;
  }
  .event-line.title { margin-top: 26px; }
  .event-line.time { margin-top: 26px; }
  .motto-word {
    position: absolute;
    left: 0;
    top: 600px;
  }
  .quote-box {
    position: absolute;
    left: 38px;
    top: 1003px;
    width: 770px;
    height: 57px;
    background: var(--ink);
    color: var(--dark);
    display: flex;
    align-items: center;
    justify-content: center;
    font-size: 35px;
    font-weight: 700;
    margin: 0;
  }
  .address {
    position: absolute;
    left: 0;
    width: 846px;
    top: 1107px;
    text-align: center;
    margin: 0;
    font-size: 38px;
    font-weight: 200;
  }
</style>
</head>
<body>
<main class="card">
  <div class="fire-photo" role="img" aria-label="Foto eines lodernden Lagerfeuers mit Funken vor dunklem Hintergrund"></div>

  <p class="date-day">30.</p>
  <p class="date-month">NOVEMBER 2018</p>

  <header class="event-info">
    <h1 class="company-name">FIRMENNAME</h1>
    <p class="event-line title">20 JÄHRIGES FIRMENJUBILÄUM</p>
    <p class="event-line time">BEGINN UM 17 UHR</p>
  </header>

  <svg class="motto-word" width="846" height="340" viewBox="0 0 846 340" aria-label="FEUER">
    <text x="0" y="333" fill="#ffffff" font-family="Saira Condensed, Arial Narrow, sans-serif" font-weight="800" font-size="382" textLength="846" lengthAdjust="spacingAndGlyphs">FEUER</text>
  </svg>

  <p class="quote-box">In dir muss brennen, was du in Anderen entzünden willst.</p>

  <p class="address">MUSTERSTRASSE 1A, 12345 STADT</p>
</main>
</body>
</html>
```